K & R Acre Works. Business card design

We need a business card designed for a new business. We have a bulldozer and tractor service. We clear land and make wildlife food plots. We provide disking, bush hogging, and site prep services.
I have attached an image of a business card that I like and would like my business cards to look similar.

Target Market(s)

anyone needing bulldozer and/or tractor services

Industry/Entity Type

Business

Contact Information for Business Card

K & R Acre Works, Operated by 7-T-Ranch
Wade Colton
601-472-3358
wcr4817@fieldmail-example.com

Font styles to use
Sans Serif

Colors

Designer to choose colors to be used in the design.

Requirements
Must have
• image of tractor and bulldozer
• Land Clearing
• Wildlife food plots
• Bush Hogging
• Disking
• Site prep
Nice to have
• i have included a image of a business card that i like. I would like mine to be similar.

```html
<!DOCTYPE html>
<html lang="en">
<head>
<meta charset="utf-8">
<title>K &amp; R Acre Works — Business Card</title>
<link rel="stylesheet" href="https://fonts.googleapis.com/css2?family=Oswald:wght@300;400;500;600&display=swap">
<style>
  :root {
    --page-bg: #2b2420;
    --card-dark: #1c2418;
    --card-green: #34452b;
    --tractor-red: #b8321f;
    --accent-red: #e2483a;
    --text-white: #f4f1ec;
    --rule-white: rgba(255,255,255,0.85);
  }
  * { margin: 0; padding: 0; box-sizing: border-box; }
  html, body {
    width: 1200px; height: 1023px; overflow: hidden;
    background: var(--page-bg);
  }
  .canvas {
    position: relative; width: 1200px; height: 1023px;
    display: flex; align-items: center; justify-content: center;
  }
  .card {
    position: relative; width: 1050px; height: 600px;
    border-radius: 26px; overflow: hidden;
    font-family: 'Oswald', sans-serif; color: var(--text-white);
    box-shadow: 0 20px 50px rgba(0,0,0,0.5);
  }
  .card-photo {
    position: absolute; inset: 0;
    background:
      radial-gradient(ellipse 38% 34% at 52% 58%, rgba(184,50,31,0.85), rgba(184,50,31,0) 70%),
      radial-gradient(ellipse 60% 70% at 40% 40%, var(--card-green), var(--card-dark) 80%);
  }
  .card-shade {
    position: absolute; inset: 0;
    background: linear-gradient(90deg, rgba(0,0,0,0.35), rgba(0,0,0,0.1) 50%, rgba(0,0,0,0.4));
  }
  .company {
    position: absolute; left: 70px; bottom: 70px;
  }
  .company-name {
    font-size: 50px; font-weight: 500; letter-spacing: 0.5px;
    text-transform: uppercase; line-height: 1;
  }
  .company-operator {
    margin-top: 10px; font-size: 25px; font-weight: 300;
    letter-spacing: 5px; text-transform: uppercase; color: var(--accent-red);
  }
  .divider {
    position: absolute; left: 525px; top: 140px;
    width: 2px; height: 300px; background: var(--rule-white);
  }
  .contact {
    position: absolute; left: 555px; top: 55px;
  }
  .person-name {
    font-size: 62px; font-weight: 600; color: var(--accent-red);
    text-transform: uppercase; line-height: 1; letter-spacing: 0;
  }
  .contact-line {
    display: flex; align-items: center; gap: 12px;
    font-size: 26px; font-weight: 300; margin-top: 12px;
  }
  .contact-line svg { width: 20px; height: 20px; flex: none; }
  .services {
    list-style: none; margin-top: 26px;
  }
  .services li {
    font-size: 32px; font-weight: 500; text-transform: uppercase;
    line-height: 1.3;
  }
</style>
</head>
<body>
<div class="canvas">
  <div class="card">
    <div class="card-photo" role="img" aria-label="Photograph of a red tractor with front loader standing among green trees and brush"></div>
    <div class="card-shade"></div>

    <div class="company">
      <div class="company-name">K &amp; R Acre Works</div>
      <div class="company-operator">Operated by 7-T-Ranch</div>
    </div>

    <div class="divider"></div>

    <div class="contact">
      <div class="person-name">Wade Colton</div>
      <div class="contact-line">
        <svg viewBox="0 0 20 20" aria-hidden="true"><path d="M5 2 L8 6 L6 8 Q8 12 12 14 L14 12 L18 15 L16 18 Q8 18 2 6 Z" fill="none" stroke="#e2483a" stroke-width="1.6" stroke-linejoin="round"/></svg>
        <span>601-472-3358</span>
      </div>
      <div class="contact-line">
        <svg viewBox="0 0 20 20" aria-hidden="true"><rect x="2" y="4" width="16" height="12" fill="none" stroke="#e2483a" stroke-width="1.6"/><path d="M2 4 L10 11 L18 4" fill="none" stroke="#e2483a" stroke-width="1.6"/></svg>
        <span>wcr4817@fieldmail-example.com</span>
      </div>
      <ul class="services">
        <li>Land Clearing</li>
        <li>Wildlife Food Plots</li>
        <li>Bush Hogging</li>
        <li>Disking - Siteprep</li>
      </ul>
    </div>
  </div>
</div>
</body>
</html>
```